New Template, new corporate image Kelvoran 2022

New template designs for google slides or PowerPoint. Match to new corporate image. The new website www.kelvoran-mx.example Needs to match our new version. Technology and Artificial Intelligence elements to reflect our type of work.
We are adding old version of template and will send elements for the new corporate images.
Please consider our website as the main corporate image.
Our templates are being used on customer presentations, webminars, internal work only.
We have our main name of company Kelvoran. Kelvoran has to be in all the templates.
Secondary logo or branded service is: Vastrelim.

Target Market(s)

Industrial users. Asset managers. Corporate visitors and customers.

Industry/Entity Type

Automotive. Chemical. Food and Beverage. Manufacturing

Other font styles liked:
• GE INSPIRA. RALEWAY

Colors
0054AA
0677BA
7BADD7
CADEEF
E8F1F8

Requirements
Must have
• Match to our elements on the new image. Use Brain Icons. Chips icons to connect equipments with software and control. Innovation.
Nice to have
• Unique images, machine images. Connecting machines and data elements. Template version for google slides. Image for industrial software for control equipment and saving money to manufacturers. Segments: Automotive, Chemical, Food and Beverages, Mining and pharmaceutical, Energy Management
Should not have
• old elements. not to much images of medical devices. Do not seems like a hospital.

```html
<!DOCTYPE html>
<html lang="en">
<head>
<meta charset="utf-8">
<title>Kelvoran — Presentation Template 2022</title>
<link href="https://fonts.googleapis.com/css2?family=Montserrat:wght@400;500;600;700;800;900&display=swap" rel="stylesheet">
<style>
:root{
  --page:#e4e4e4;
  --blue:#0b45b0;
  --blue-deep:#08399a;
  --blue-bright:#1565c8;
  --navy:#0a1530;
  --navy-2:#0d1c3d;
  --card:#0d5cc0;
  --sky:#7badd7;
  --ice:#cadeef;
  --white:#ffffff;
}
*{margin:0;padding:0;box-sizing:border-box}
html,body{width:1200px;height:4335px;overflow:hidden;background:var(--page)}
body{font-family:"Montserrat",Arial,sans-serif;color:var(--white);position:relative}
.slide{position:absolute;left:35px;width:1130px;height:636px;overflow:hidden}
.s1{top:67px;background:var(--navy)}
.s2{top:779px;background:linear-gradient(135deg,var(--blue) 0%,var(--blue-deep) 100%)}
.s3{top:1493px;background:linear-gradient(120deg,var(--navy-2),var(--navy))}
.s4{top:2206px;background:radial-gradient(circle at 50% 40%,#1256c4,var(--blue-deep))}
.s5{top:2920px;background:linear-gradient(180deg,#141d33,#0c1428)}
.s6{top:3633px;background:linear-gradient(180deg,#0b48b8,#0a3fa4)}
.abs{position:absolute}
.brand{position:absolute;display:flex;align-items:center;gap:10px;font-weight:600;font-size:30px;letter-spacing:.5px;color:var(--white)}
.brand .mark{width:14px;height:14px;background:var(--white)}
.pagenum{position:absolute;font-size:13px;font-weight:500;color:var(--white)}
.photo{position:absolute}
.s1 .title{position:absolute;right:40px;top:300px;font-size:66px;font-weight:700;letter-spacing:-1px}
.s1 .lead{position:absolute;right:40px;top:390px;width:440px;text-align:right;font-size:14px;line-height:26px;font-weight:400}
.h2{font-weight:700;font-size:34px;line-height:1.3}
.s2 .h2{position:absolute;left:32px;top:150px}
.s2 .body{position:absolute;left:32px;top:225px;width:520px;font-size:11.6px;line-height:21px}
.s2 .body p{margin-bottom:21px}
.frame{position:absolute;border:1.5px solid rgba(255,255,255,.55)}
.s3 .h2{position:absolute;left:560px;top:170px;width:520px}
.s3 ul{position:absolute;left:565px;top:280px;width:500px;list-style:none;font-size:11px;line-height:20px}
.s3 li{position:relative;padding-left:20px;margin-bottom:5px}
.s3 li svg{position:absolute;left:0;top:5px}
.s3 .note{position:absolute;left:565px;top:455px;width:500px;font-size:12px;line-height:20px}
.s4 .side{position:absolute;text-align:center;font-size:11px;line-height:24px}
.s4 .side h3{font-size:24px;font-weight:600;line-height:30px;margin-bottom:14px}
.s4 .partners-h{font-size:20px;font-weight:600;margin-top:22px}
.badge{display:inline-block;width:78px;height:22px;background:rgba(255,255,255,.85);margin:12px 6px 0}
.badge.orange{background:#e2762c}
.s5 .h2{position:absolute;left:0;width:100%;top:55px;text-align:center;font-size:36px}
.card{position:absolute;width:214px;height:198px;background:var(--card);padding:110px 12px 0;font-size:9.5px;line-height:18px;color:#dce8f7}
.card .icon{position:absolute;left:10px;top:0;width:64px;height:74px;background:#0a2658;display:flex;align-items:center;justify-content:center}
.s6 .thanks{position:absolute;left:0;width:100%;top:270px;text-align:center;font-size:66px;font-weight:900;letter-spacing:-1px}
.s6 .band{position:absolute;left:0;bottom:0;width:100%;height:116px;background:#0b2a66}
.contact{position:absolute;top:27px;display:flex;align-items:flex-start;gap:14px}
.contact .dot{width:57px;height:57px;border-radius:50%;background:#1762c9;display:flex;align-items:center;justify-content:center;flex:none}
.contact .lbl{font-size:15px;font-weight:600;margin-top:8px}
.contact .val{font-size:16px;font-weight:500}
.contact .val.small{font-size:11.5px;line-height:18px;width:220px;font-weight:400}
</style>
</head>
<body>

<!-- Slide 1: cover -->
<section class="slide s1">
  <div class="photo" role="img" aria-label="Glowing blue digital brain above a circuit chip" style="left:0;top:0;width:900px;height:636px;background:radial-gradient(circle at 33% 35%,#2a9fe0 0%,#0f4f86 18%,#071426 48%,#03070f 100%)"></div>
  <svg class="abs" style="left:0;top:0" width="1130" height="636" viewBox="0 0 1130 636">
    <polygon points="806,0 1130,0 1130,636 604,636" fill="#0b4ab6"/>
    <line x1="810" y1="0" x2="604" y2="636" stroke="#3d8be8" stroke-width="3"/>
  </svg>
  <div class="brand" style="right:42px;top:68px"><span class="mark"></span>kelvoran</div>
  <div class="title">Kelvoran.</div>
  <p class="lead">We are specialists in automation, process control, information technologies, development and consulting for quality, efficiency and production. Our goal is to always provide the best solutions in conjunction with our technology partners Norvane.</p>
  <div class="pagenum" style="right:24px;top:600px">| 1 |</div>
</section>

<!-- Slide 2: hyper digitalization -->
<section class="slide s2">
  <div class="brand" style="left:32px;top:52px"><span class="mark"></span>kelvoran</div>
  <h2 class="h2">About Hyper Digitalization</h2>
  <div class="body">
    <p>We know that technology advanced dramatically in all environments: personnel, processes, artificial intelligence, mobility, interconnectivity, cloud, etc., without expecting it, hyper digitalization became part of us, it is the day-to-day in many decisions and the industry along with your assets are no exception</p>
    <p>New industrial challenges now raise questions: How to master the concept "hyperdigitalize"? How to take advantage of this? Do we have digital governments in place that successful businesses and operations? Do we have the infrastructure available? Are we trained to do it?</p>
    <p>If we take into account that the production assets are equipment with several years of operation, with little to no digital communication capacity, with different protocols, obsolescence or technical ignorance. Kelvoran proposes that it is time to create a hyper digitalization strategy for your industrial assets.</p>
    <p>When the plant has a multiplicity of equipment to connect, the complexity of this increases. Data is lost or does not reach its primary destination.</p>
  </div>
  <div class="frame" style="left:630px;top:0;width:0;height:215px;border-width:0 0 0 1.5px"></div>
  <div class="frame" style="left:630px;top:215px;width:480px;height:0;border-width:1.5px 0 0 0"></div>
  <div class="frame" style="left:630px;top:370px;width:0;height:200px;border-width:0 0 0 1.5px"></div>
  <div class="frame" style="left:630px;top:570px;width:170px;height:0;border-width:1.5px 0 0 0"></div>
  <div class="frame" style="left:935px;top:0;width:0;height:260px;border-width:0 0 0 1.5px"></div>
  <div class="photo" role="img" aria-label="Dark circuit board with a central AI processor chip" style="left:565px;top:29px;width:286px;height:286px;background:radial-gradient(circle at 45% 55%,#2a5e8a,#0d1f33 60%,#070e18)"></div>
  <div class="photo" role="img" aria-label="White humanoid robot in a thinking pose with a visible digital brain" style="left:801px;top:276px;width:284px;height:332px;background:linear-gradient(160deg,#1f3c7a,#0a1c44 60%,#061430)"></div>
  <div class="pagenum" style="left:10px;top:612px">| 2 |</div>
</section>

<!-- Slide 3: APM strategy -->
<section class="slide s3">
  <svg class="abs" style="left:0;top:0" width="1130" height="636" viewBox="0 0 1130 636">
    <polygon points="0,0 330,0 0,260" fill="#0d4bb3"/>
    <polygon points="0,636 0,510 330,636" fill="#0d4bb3"/>
    <polygon points="460,636 560,560 600,636" fill="#0d4bb3"/>
    <polyline points="940,0 1070,125 1130,65" fill="none" stroke="#ffffff" stroke-width="1.2" opacity=".7"/>
    <line x1="40" y1="636" x2="150" y2="550" stroke="#ffffff" stroke-width="1" opacity=".6"/>
  </svg>
  <div class="brand" style="left:14px;top:48px"><span class="mark"></span>kelvoran</div>
  <div class="photo" role="img" aria-label="White robot holding a digital tablet" style="left:91px;top:125px;width:441px;height:443px;background:linear-gradient(90deg,#d9dde3,#ffffff 55%)"></div>
  <h2 class="h2">In which cases does an APM strategy apply?</h2>
  <ul>
    <li><svg width="11" height="11" viewBox="0 0 11 11"><circle cx="5.5" cy="5.5" r="5.5" fill="#fff"/><path d="M3 5.6l1.7 1.7L8 4" stroke="#0a1530" stroke-width="1.4" fill="none"/></svg>When an asset spends more than expected in energy resources, efficiency and constantly presents failures that affect production.</li>
    <li><svg width="11" height="11" viewBox="0 0 11 11"><circle cx="5.5" cy="5.5" r="5.5" fill="#fff"/><path d="M3 5.6l1.7 1.7L8 4" stroke="#0a1530" stroke-width="1.4" fill="none"/></svg>When maintenance budget constraints make it critical to reduce costs.</li>
    <li><svg width="11" height="11" viewBox="0 0 11 11"><circle cx="5.5" cy="5.5" r="5.5" fill="#fff"/><path d="M3 5.6l1.7 1.7L8 4" stroke="#0a1530" stroke-width="1.4" fill="none"/></svg>To attend unplanned downtime events with a greater strategic impact.</li>
    <li><svg width="11" height="11" viewBox="0 0 11 11"><circle cx="5.5" cy="5.5" r="5.5" fill="#fff"/><path d="M3 5.6l1.7 1.7L8 4" stroke="#0a1530" stroke-width="1.4" fill="none"/></svg>In assets that can never fail, guaranteeing their availability.</li>
    <li><svg width="11" height="11" viewBox="0 0 11 11"><circle cx="5.5" cy="5.5" r="5.5" fill="#fff"/><path d="M3 5.6l1.7 1.7L8 4" stroke="#0a1530" stroke-width="1.4" fill="none"/></svg>When looking to change from planned or corrective maintenance activities to a predictive maintenance model.</li>
  </ul>
  <p class="note">We invite you to learn more about APM's strategy. Kelvoran represents software leaders with the best Asset Performance practices who are sure to be of great help in solving complex challenges.</p>
  <div class="pagenum" style="right:14px;top:605px">| 3 |</div>
</section>

<!-- Slide 4: Edge -->
<section class="slide s4">
  <div class="brand" style="left:0;right:0;justify-content:center;top:38px"><span class="mark"></span>kelvoran</div>
  <div class="frame" style="left:330px;top:170px;width:444px;height:380px"></div>
  <div class="photo" role="img" aria-label="Robotic gripper arm reaching toward a human hand over a white circular interface" style="left:362px;top:116px;width:379px;height:485px;border:3px solid #dfe8f4;background:radial-gradient(circle at 50% 45%,#ffffff,#e7edf3 55%,#c9d7e2)"></div>
  <div class="side" style="left:25px;top:224px;width:300px">
    <h3>What do we mean<br>by Edge</h3>
    <p>Edge is the last technological link to integrate production equipment to the industrial internet, and these must have the computing capacity and connectivity for infrastructure to support all digitization requirements.</p>
    <p class="partners-h">Partners</p>
    <span class="badge"></span><span class="badge orange"></span>
  </div>
  <div class="side" style="left:785px;top:205px;width:320px">
    <h3>Edge hardware and<br>software examples</h3>
    <p>Computers integrated to production control, located on the plant floor and with low cost.</p>
    <p>Hardware capable of multiple signals, vibration, temperature and motion control capable of pattern recognition and new artificial intelligence functions.</p>
    <p>Controllers for multiple points, with performance and reading capabilities in diverse protocols.</p>
    <p>Smart sensors and rfid tracking devices for asset identification and production tracking</p>
  </div>
  <div class="pagenum" style="right:14px;top:605px">| 4 |</div>
</section>

<!-- Slide 5: industrial data hub -->
<section class="slide s5">
  <h2 class="h2">Where to apply an industrial data hub?</h2>
  <div class="card" style="left:219px;top:145px">
    <div class="icon"><svg width="36" height="36" viewBox="0 0 36 36" fill="none" stroke="#fff" stroke-width="1.6"><path d="M18 9a7 7 0 0 0-4 12.7V25h8v-3.3A7 7 0 0 0 18 9z"/><path d="M15 28h6M18 3v3M8 8l2 2M28 8l-2 2M4 17h3M29 17h3"/></svg></div>
    In production plants with multiple automation equipment, PLC, PAC and various scattered sensors, with difficulty in obtaining a numerical record of their behavior.
  </div>
  <div class="card" style="left:458px;top:145px">
    <div class="icon"><svg width="36" height="36" viewBox="0 0 36 36" fill="none" stroke="#fff" stroke-width="1.6"><rect x="10" y="6" width="18" height="24"/><path d="M7 9v24h18M14 12h10M14 16h10M14 20h10M14 24h6"/></svg></div>
    When the digital records of the production asset are not consistent with the reality of the process or production.
  </div>
  <div class="card" style="left:695px;top:145px">
    <div class="icon"><svg width="40" height="36" viewBox="0 0 40 36" fill="none" stroke="#fff" stroke-width="1.6"><circle cx="20" cy="12" r="4"/><circle cx="10" cy="15" r="3"/><circle cx="30" cy="15" r="3"/><path d="M12 28a8 8 0 0 1 16 0zM4 27a6 6 0 0 1 8-5M36 27a6 6 0 0 0-8-5"/></svg></div>
    In multiple work teams, production, processes that require a high degree of synchronization to carry out the work together.
  </div>
  <div class="card" style="left:338px;top:372px">
    <div class="icon"><svg width="36" height="36" viewBox="0 0 36 36" fill="#fff"><rect x="9" y="4" width="18" height="3"/><rect x="9" y="29" width="18" height="3"/><path d="M11 7h14l-6 11 6 11H11l6-11z" fill="none" stroke="#fff" stroke-width="1.6"/><path d="M14 27h8l-4-6z"/></svg></div>
    In different assets with different denominations and years of age that require a great effort to be able to connect.
  </div>
  <div class="card" style="left:576px;top:372px">
    <div class="icon"><svg width="36" height="36" viewBox="0 0 36 36" fill="none" stroke="#fff" stroke-width="1.6"><path d="M10 25h17a5 5 0 0 0 0-10 8 8 0 0 0-15-1 5.5 5.5 0 0 0-2 11z"/></svg></div>
    In multiple protocols and diverse indicator needs now related in the corporate cloud.
  </div>
  <div class="brand" style="left:35px;top:570px"><span class="mark"></span>kelvoran</div>
  <div class="pagenum" style="right:14px;top:605px">| 5 |</div>
</section>

<!-- Slide 6: closing -->
<section class="slide s6">
  <div class="photo" role="img" aria-label="Faint isometric blue cubes and circuit board background" style="left:330px;top:100px;width:480px;height:420px;background:radial-gradient(ellipse at 50% 45%,rgba(90,140,220,.35),rgba(11,72,184,0) 70%)"></div>
  <div class="thanks">THANK YOU</div>
  <div class="band">
    <div class="contact" style="left:160px">
      <div class="dot"><svg width="22" height="22" viewBox="0 0 24 24" fill="#fff"><path d="M6.6 10.8a15 15 0 0 0 6.6 6.6l2.2-2.2c.3-.3.7-.4 1-.2 1.1.4 2.3.6 3.6.6.6 0 1 .4 1 1V20c0 .6-.4 1-1 1A17 17 0 0 1 3 4c0-.6.4-1 1-1h3.5c.6 0 1 .4 1 1 0 1.3.2 2.5.6 3.6.1.3 0 .7-.2 1z"/></svg></div>
      <div><div class="lbl">CALL NOW</div><div class="val">+52 81 5550 0142</div></div>
    </div>
    <div class="contact" style="left:417px">
      <div class="dot"><svg width="22" height="22" viewBox="0 0 24 24" fill="#fff"><path d="M3 6h18v12H3z"/><path d="M3 6l9 7 9-7" stroke="#1762c9" stroke-width="1.8" fill="none"/></svg></div>
      <div><div class="lbl">EMAIL NOW</div><div class="val">info@kelvoran-mx.example</div></div>
    </div>
    <div class="contact" style="left:723px">
      <div class="dot"><svg width="20" height="24" viewBox="0 0 20 24" fill="#fff"><path d="M10 1a8 8 0 0 0-8 8c0 6 8 14 8 14s8-8 8-14a8 8 0 0 0-8-8zm0 11a3 3 0 1 1 0-6 3 3 0 0 1 0 6z"/></svg></div>
      <div><div class="lbl">ADDRESS</div><div class="val small">Monterrey, NL Calle Ficticia # 120, Col. Valle Norte</div></div>
    </div>
  </div>
</section>

</body>
</html>
```